Billboard design for dentist that sees only children

I own a 12' x 25' digital billboard and I need help with billboard design. My wife is a general dentist that only sees children and is very passionate about giving them a quality dental experience . She has a great reputation in town. Obviously with a billboard there can't be a lot of reading. Maybe something that shows safety, love, experience and children. I am completely open to your ideas. In addition I have other businesses that also need billboard design so this could lead to more work. If you go to Maplecovedental.com under the about section you will find more information about the practice and our phone number. Attached is our logo which could be changed and content specs for the digital billboard. Happy Designing!!

Target Market(s)

Parents with children

Colors

Designer to choose colors to be used in the design.

Requirements
Must have
• Must attract attention and be nice to look at.
Nice to have
• Probably should have children in the picture ..... Maybe
Should not have
• If I see something I don't like I will let you know

```html
<!DOCTYPE html>
<html lang="en">
<head>
<meta charset="utf-8">
<title>Maple Cove Dental – Billboard</title>
<link href="https://fonts.googleapis.com/css2?family=Montserrat:wght@500;600;700&family=Open+Sans:ital,wght@0,400;0,600;1,400&display=swap" rel="stylesheet">
<style>
  :root {
    --page-bg: #e6ebef;
    --frame: #d9dde1;
    --board-bg: #f7f8f9;
    --headline: #2f7565;
    --navy: #2b3768;
    --pill: #3b56a6;
    --white: #ffffff;
    --tagline: #3a8fc4;
    --photo-light: #eef3f6;
    --photo-mid: #d9e6ee;
    --photo-warm: #f0d2bf;
    --photo-hair: #e6c98f;
    --photo-teal: #7fa79a;
  }
  * { margin: 0; padding: 0; box-sizing: border-box; }
  html, body {
    width: 1200px; height: 731px; overflow: hidden;
    background: var(--page-bg);
  }
  .billboard {
    position: absolute; left: 34px; top: 84px;
    width: 1132px; height: 564px;
    background: var(--frame);
    padding: 7px;
    box-shadow: 0 6px 18px rgba(0,0,0,0.12);
  }
  .board {
    position: relative; width: 100%; height: 100%;
    background: linear-gradient(90deg, var(--board-bg) 0%, #f1f3f5 60%, #eceff2 100%);
    overflow: hidden;
  }
  .photo {
    position: absolute; right: 0; top: 0; width: 62%; height: 100%;
    background:
      radial-gradient(ellipse 24% 34% at 72% 40%, var(--photo-warm) 0%, rgba(240,210,191,0) 100%),
      radial-gradient(ellipse 22% 40% at 82% 30%, var(--photo-hair) 0%, rgba(230,201,143,0) 100%),
      radial-gradient(ellipse 20% 45% at 92% 75%, var(--photo-teal) 0%, rgba(127,167,154,0) 100%),
      radial-gradient(ellipse 30% 22% at 62% 92%, #8cc9e3 0%, rgba(140,201,227,0) 100%),
      linear-gradient(90deg, rgba(247,248,249,1) 0%, rgba(238,243,246,0.6) 30%, var(--photo-mid) 100%);
  }
  .headline {
    position: absolute; left: 64px; top: 64px;
    font-family: "Montserrat", sans-serif; color: var(--headline);
  }
  .headline__lead { display: block; font-size: 40px; font-weight: 600; line-height: 1.1; }
  .headline__main {
    display: block; margin-left: 33px; margin-top: 8px;
    font-size: 43px; font-weight: 700; line-height: 1.1; letter-spacing: 0.5px;
  }
  .cta-label {
    position: absolute; left: 83px; top: 250px;
    font-family: "Open Sans", sans-serif; font-weight: 600; font-size: 15px;
    color: var(--navy); letter-spacing: 0.2px;
  }
  .phone-pill {
    position: absolute; left: 79px; top: 278px; width: 384px; height: 63px;
    background: var(--pill); border-radius: 12px;
    display: flex; align-items: center; justify-content: center; gap: 14px;
    font-family: "Open Sans", sans-serif; font-weight: 600; font-size: 40px; color: var(--white);
  }
  .phone-pill svg { width: 30px; height: 30px; }
  .brand { position: absolute; left: 46px; top: 404px; display: flex; align-items: center; gap: 12px; }
  .brand__dot { width: 52px; height: 52px; border-radius: 50%; background: var(--headline); }
  .brand__name {
    font-family: "Open Sans", sans-serif; font-weight: 400; font-size: 37px;
    color: var(--headline); line-height: 1;
  }
  .brand__tagline {
    display: block; margin-top: 2px; text-align: right;
    font-family: "Open Sans", sans-serif; font-style: italic; font-size: 16px; color: var(--tagline);
  }
  .address {
    position: absolute; left: 46px; top: 510px;
    font-family: "Open Sans", sans-serif; font-size: 16px; color: var(--navy);
  }
</style>
</head>
<body>
  <div class="billboard">
    <div class="board">
      <div class="photo" role="img" aria-label="Photo of a smiling child in a dental chair with a dentist holding a mirror"></div>

      <h1 class="headline">
        <span class="headline__lead">We Love Kids and Know</span>
        <span class="headline__main">HOW TO CARE FOR THEM</span>
      </h1>

      <p class="cta-label">CALL OR SCHEDULE YOUR APPOINTMENT ONLINE!</p>

      <div class="phone-pill">
        <svg viewBox="0 0 24 24" aria-hidden="true">
          <circle cx="12" cy="12" r="11" fill="none" stroke="#fff" stroke-width="1.6"/>
          <path d="M8.6 6.8c.4-.3 1-.2 1.2.2l1 2c.2.4.1.8-.2 1.1l-.8.7c.5 1.2 1.4 2.2 2.6 2.8l.7-.8c.3-.3.8-.4 1.1-.2l2 1c.4.2.5.8.2 1.2l-.9 1.1c-.4.5-1.1.7-1.7.5-3-1-5.3-3.3-6.2-6.3-.2-.6 0-1.3.5-1.7z" fill="#fff"/>
        </svg>
        <span>555-014-2280</span>
      </div>

      <div class="brand">
        <span class="brand__dot" aria-hidden="true"></span>
        <div>
          <span class="brand__name">Maple Cove Dental</span>
          <span class="brand__tagline">general dentistry for children</span>
        </div>
      </div>

      <p class="address">45 HARBOR LANE, MAPLE COVE, CA</p>
    </div>
  </div>
</body>
</html>
```